Innovative Media Company needs Web Design

We need a web design for a new multimedia product that we are launching to potential partners and investors. The initial website we are looking to launch consists of three pages:
1.) A home/feature set page
2.) An account landing page
3.) An about us page
We would like the style of our website to be VERY similar to the following site: http://www.brintaro.com/tundra.
We have worked a bit on this project with a previous designer but were not happy with the results. As a guideline, you may refer to their previous work and the Tundra 88 website.
We realize this prize is a bit low for this project. However, there is a great opportunity for follow-on work. We are hoping to make a long-term business relationship with a high quality web-developer.
Attached are the product logo and our previous designer's work. Please let me know if you have any questions.
Thank you.
All,
Thanks for your submissions. Please note that rather than have headers that state "Enhanced TV Functionality" and "Seamless Device Integration", I would like to see all features (the six or seven boxes) in the same section. Also, please revise your designs to have the following statement below the picture that stretches across the screen and above the feature descriptions:
"Available via apps for the television and mobile devices,
naLix technology integrates numerous media components to provide users with
enhanced TV functionality and seamless device integration for an unparalleled
personalized viewing experience."
Thanks you.

```html
<!DOCTYPE html>
<html lang="en">
<head>
<meta charset="utf-8">
<title>naLix</title>
<link href="https://fonts.googleapis.com/css2?family=PT+Sans:wght@400;700&family=PT+Sans+Narrow:wght@400;700&display=swap" rel="stylesheet">
<style>
  :root {
    --header-dark: #4a4a4a;
    --header-line: #3c3c3c;
    --orange: #f27a1f;
    --orange-dark: #d85f0c;
    --text-body: #3a3a3a;
    --text-light: #ffffff;
    --panel-grey: #e6e7e9;
    --feature-grey: #aeaeae;
    --social-grey: #6b6b6b;
    --rule: #d6d6d6;
  }
  * { margin: 0; padding: 0; box-sizing: border-box; }
  html, body { width: 867px; height: 1200px; overflow: hidden; background: #fff; }
  body { position: relative; font-family: "PT Sans", Arial, sans-serif; color: var(--text-body); }
  .abs { position: absolute; }

  /* header */
  .site-header { left: 0; top: 0; width: 867px; height: 122px; background: var(--header-dark); border-bottom: 2px solid var(--header-line); }
  .brand { left: 128px; top: 30px; display: flex; align-items: center; gap: 8px; }
  .brand-dot { width: 22px; height: 22px; border-radius: 50%; background: var(--text-light); }
  .brand-name { font-size: 30px; font-weight: 700; color: var(--text-light); letter-spacing: 0.5px; }
  .search { left: 571px; top: 45px; width: 167px; height: 19px; border-radius: 5px; background: linear-gradient(#d6d6d6, #b9b9b9); border: 1px solid #8a8a8a; font-size: 9px; color: #555; padding: 3px 0 0 8px; }
  .search svg { position: absolute; right: 4px; top: 2px; }
  .main-nav { left: 340px; top: 86px; display: flex; gap: 5px; }
  .nav-btn { width: 77px; height: 22px; border-radius: 4px; background: linear-gradient(#ffffff, #dcdcdc); box-shadow: 0 2px 2px rgba(0,0,0,.45); font-size: 9px; color: #222; text-align: center; line-height: 22px; }

  /* hero */
  .hero { left: 0; top: 124px; width: 867px; height: 292px; background: radial-gradient(ellipse at 55% 45%, #ffffff 30%, #e9e9e9 65%, #cfcfcf 100%); }
  .hero-title { left: 169px; top: 158px; font-family: "PT Sans Narrow", Arial, sans-serif; font-size: 21px; color: #1e1e1e; }
  .hero-text { left: 169px; top: 188px; width: 240px; font-size: 9.2px; line-height: 15.5px; text-align: justify; color: #222; }
  .btn-more { left: 169px; top: 269px; width: 76px; height: 24px; border-radius: 3px; background: linear-gradient(#f79a45, var(--orange-dark)); box-shadow: 0 2px 3px rgba(0,0,0,.35); color: #fff; font-family: "PT Sans Narrow", Arial, sans-serif; font-size: 13px; line-height: 24px; padding-left: 16px; }
  .hero-arrow { top: 240px; }
  .hero-photo { left: 415px; top: 142px; width: 312px; height: 268px; border-radius: 10px; background: linear-gradient(160deg, #2b2f36 0%, #3a4a6a 40%, #9aa3ad 75%, #f3f3f3 100%); opacity: .9; }

  /* content frame */
  .content-frame { left: 109px; top: 416px; width: 650px; height: 655px; border: 1px dashed #cfcfcf; border-top: none; }
  .section-title { font-size: 20px; color: var(--orange); text-align: center; }
  .welcome-title { left: 127px; top: 427px; width: 613px; }
  .welcome-rule { left: 127px; top: 456px; width: 613px; height: 1px; background: var(--rule); }
  .welcome-brand { left: 126px; top: 473px; width: 95px; height: 109px; background: var(--header-dark); display: flex; align-items: center; justify-content: center; gap: 5px; }
  .welcome-brand .brand-dot { width: 12px; height: 12px; }
  .welcome-brand .brand-name { font-size: 20px; }
  .welcome-text { left: 245px; top: 472px; width: 493px; font-size: 8.4px; line-height: 17.6px; text-align: justify; }
  .shadow-rule { left: 126px; width: 615px; height: 14px; background: radial-gradient(ellipse at 50% 0%, rgba(0,0,0,.18), rgba(0,0,0,0) 70%); }

  /* product info */
  .product-panel { left: 128px; top: 617px; width: 612px; height: 148px; background: var(--panel-grey); box-shadow: 0 4px 6px rgba(0,0,0,.2); }
  .product-title { left: 128px; top: 624px; width: 612px; font-size: 16px; }
  .product-rule { left: 128px; top: 651px; width: 612px; height: 1px; background: #cfd0d2; }
  .product-photo { left: 145px; top: 663px; width: 165px; height: 102px; background: linear-gradient(90deg, #c99a7a 0%, #2c2c2c 18%, #dcdcdc 40%, #bdbdbd 70%, #2c2c2c 85%, #c99a7a 100%); }
  .product-text { left: 330px; top: 661px; width: 385px; font-size: 8.4px; line-height: 15.6px; text-align: justify; }
  .btn-read { left: 331px; top: 731px; width: 63px; height: 19px; border-radius: 3px; background: linear-gradient(#f79a45, var(--orange-dark)); color: #fff; font-size: 8.5px; line-height: 19px; text-align: center; box-shadow: 0 1px 2px rgba(0,0,0,.3); }

  /* feature */
  .feature-photo { left: 126px; top: 805px; width: 115px; height: 148px; background: linear-gradient(150deg, #1d2430 0%, #50606e 45%, #2a2a2a 70%, #d9d9d9 100%); }
  .feature-panel { left: 241px; top: 805px; width: 499px; height: 148px; background: var(--feature-grey); }
  .feature-title { left: 261px; top: 817px; font-size: 15.5px; color: #1e1e1e; }
  .feature-rule { left: 261px; top: 841px; width: 463px; height: 1px; background: #c8c8c8; }
  .feature-sub { left: 262px; top: 858px; font-size: 12.5px; color: #111; }
  .feature-text { left: 262px; top: 876px; width: 450px; font-size: 9.2px; line-height: 15.5px; color: #222; }

  /* social */
  .social-band { left: 128px; top: 981px; width: 612px; height: 74px; background: var(--social-grey); }
  .social-names { left: 146px; top: 996px; width: 90px; height: 44px; display: flex; align-items: center; justify-content: space-between; }
  .social-name { font-size: 10px; font-weight: 700; color: #111; }
  .social-divider { width: 1px; height: 44px; background: #444; }
  .social-title { left: 256px; top: 996px; font-size: 16.5px; color: var(--text-light); }
  .social-text { left: 256px; top: 1021px; font-size: 9.5px; color: #f0f0f0; }

  /* footer */
  .site-footer { left: 0; top: 1079px; width: 867px; height: 121px; background: var(--header-dark); }
  .footer-nav { left: 0; top: 1121px; width: 867px; text-align: center; font-size: 8.8px; color: #fff; word-spacing: 2px; }
  .copyright { left: 0; top: 1141px; width: 867px; text-align: center; font-size: 8.4px; color: #fff; }
</style>
</head>
<body>
  <header class="abs site-header"></header>
  <div class="abs brand"><span class="brand-dot"></span><span class="brand-name">naLix</span></div>
  <div class="abs search">Search
    <svg width="13" height="13" viewBox="0 0 13 13"><circle cx="6.5" cy="6.5" r="6" fill="#eee" stroke="#999"/><circle cx="5.8" cy="5.8" r="2.3" fill="none" stroke="#555" stroke-width="1.2"/><line x1="7.5" y1="7.5" x2="9.6" y2="9.6" stroke="#555" stroke-width="1.4"/></svg>
  </div>
  <nav class="abs main-nav">
    <div class="nav-btn">Home</div>
    <div class="nav-btn">Product info</div>
    <div class="nav-btn">About Us</div>
    <div class="nav-btn">Contact Us</div>
    <div class="nav-btn">Help</div>
  </nav>

  <section class="abs hero"></section>
  <svg class="abs hero-arrow" style="left:114px" width="24" height="36" viewBox="0 0 24 36"><polyline points="19,3 5,18 19,33" fill="none" stroke="#9a9a9a" stroke-width="5"/></svg>
  <svg class="abs hero-arrow" style="left:733px" width="24" height="36" viewBox="0 0 24 36"><polyline points="5,3 19,18 5,33" fill="none" stroke="#9a9a9a" stroke-width="5"/></svg>
  <div class="abs hero-photo" role="img" aria-label="Photo of an open laptop showing a desktop full of windows"></div>
  <h1 class="abs hero-title">Heading</h1>
  <p class="abs hero-text">Lorem Ipsum is simply dummy text of the printing and type-setting industry. Lorem Ipsum has been the industry's standard dummy text ever since the 1500s, when an unknown printer took a galley of type and scrambled it to make a type specimen book.</p>
  <div class="abs btn-more">more &gt;&gt;</div>

  <div class="abs content-frame"></div>
  <h2 class="abs section-title welcome-title">welcome to our site</h2>
  <div class="abs welcome-rule"></div>
  <div class="abs welcome-brand"><span class="brand-dot"></span><span class="brand-name">naLix</span></div>
  <p class="abs welcome-text">Lorem Ipsum is simply dummy text of the printing and typesetting industry. Lorem Ipsum has been the industry's standard dummy text ever since the 1500s, when an unknown printer took a galley of type and scrambled it to make a type specimen book. It has survived not only five centuries, but also the leap into electronic typesetting, remaining essentially unchanged. It was popularised in the 1960s with the release of Letterform sheets containing Lorem Ipsum passages, and more recently with desktop publishing software like Folio LayoutPro including versions of Lorem Ipsum. It is a long established fact that a reader will be distracted by the readable content of a page when looking at its layout.</p>
  <div class="abs shadow-rule" style="top:600px"></div>

  <div class="abs product-panel"></div>
  <h2 class="abs section-title product-title">product info</h2>
  <div class="abs product-rule"></div>
  <div class="abs product-photo" role="img" aria-label="Photo of two hands holding a tablet showing a magazine page"></div>
  <p class="abs product-text">Lorem Ipsum is simply dummy text of the printing and typesetting industry. Lorem Ipsum has been the industry's standard dummy text ever since the 1500s, when an unknown printer took a galley of type and scrambled it to make a type specimen book. It has survived not only five centuries, but also the leap into electronic typesetting, remaining essentially unchanged. It was popularised in the 1960s with....</p>
  <div class="abs btn-read">Read More</div>
  <div class="abs shadow-rule" style="top:778px"></div>

  <div class="abs feature-photo" role="img" aria-label="Photo of a dark laptop with a water droplet wallpaper"></div>
  <div class="abs feature-panel"></div>
  <h3 class="abs feature-title" style="font-weight:400">Enhanced TV Functionality</h3>
  <div class="abs feature-rule"></div>
  <h4 class="abs feature-sub" style="font-weight:400">Schedule viewing reminders with friends and family</h4>
  <p class="abs feature-text">to join a virtual community and interact through social networking, instant messenger, or telecommunica-tions such as an audio feed.</p>
  <div class="abs shadow-rule" style="top:962px"></div>

  <div class="abs social-band"></div>
  <div class="abs social-names"><span class="social-name">Chatterly</span><span class="social-divider"></span><span class="social-name">Flitter</span></div>
  <p class="abs social-title">View a social feed containing Chatterly updates and Flits</p>
  <p class="abs social-text">pertaining to the show they are watching friends, family, and celebrities.</p>

  <footer class="abs site-footer"></footer>
  <p class="abs footer-nav">Home &nbsp;| &nbsp;Product info &nbsp;| &nbsp;About Us &nbsp;| &nbsp;Contact &nbsp;| &nbsp;Help</p>
  <p class="abs copyright">Copyrights @ 2012 All Rights Reserved</p>
</body>
</html>
```